Commercial Loan Originator Business Card (CHANGE COLORS SCHEME)

CHANGE COLOR SCHEME - SAME DESIGN

Name Marlene Agate
Title Commercial Loan Originator
Office (800) 417-2906 x68
Direct (240) 615-2043
Email freshgreens4life@quillbox.example

Name Dale Morrow
Office (800) 417-2906 x70
Direct (410) 392-5184
Email d.morthehomeguy@quillbox.example

Name Leonard Vasko
Office (800) 417-2906 x71
Direct (215) 463-0712
Email l.vasko41@quillbox.example

Name Gwen Halsey
Office (800) 417-2906 x
Direct (202) 548-1370
Email ghalsey63@quillbox.example

Name Mirna Ashby
Office (800) 417-2906 x72
Direct (240) 871-4526
Email tristatehomelending@quillbox.example

```html
<!DOCTYPE html>
<html lang="en">
<head>
<meta charset="utf-8">
<title>Marlene Agate – Business Card</title>
<link href="https://fonts.googleapis.com/css2?family=Cinzel:wght@600&family=Poppins:wght@400&display=swap" rel="stylesheet">
<style>
  :root {
    --primary: #14574a;
    --accent: #e0a526;
    --ink: #1d1d22;
    --paper: #ffffff;
    --backdrop: #e6e7ea;
    --photo-top: #f3e3d6;
    --photo-bottom: #c98a6a;
  }
  html, body {
    margin: 0;
    width: 1200px;
    height: 952px;
    overflow: hidden;
    background: var(--backdrop);
  }
  .card {
    position: absolute;
    left: 50px;
    top: 136px;
    width: 1100px;
    height: 680px;
    background: var(--paper);
    border-radius: 38px;
    overflow: hidden;
    box-shadow: 0 6px 14px rgba(0,0,0,0.25);
  }
  .accent-bar {
    position: absolute;
    left: 0;
    top: 95px;
    width: 27px;
    height: 66px;
    background: var(--primary);
  }
  .name {
    position: absolute;
    left: 50px;
    top: 90px;
    margin: 0;
    font-family: "Cinzel", serif;
    font-weight: 600;
    font-size: 47px;
    line-height: 1.1;
    color: var(--primary);
    letter-spacing: 0.3px;
  }
  .title {
    position: absolute;
    left: 50px;
    top: 138px;
    margin: 0;
    font-family: "Poppins", sans-serif;
    font-size: 31px;
    line-height: 1.2;
    color: var(--ink);
  }
  .contacts {
    position: absolute;
    left: 50px;
    top: 338px;
    margin: 0;
    padding: 0;
    list-style: none;
    font-family: "Poppins", sans-serif;
    font-size: 31px;
    color: var(--ink);
  }
  .contacts li {
    display: flex;
    align-items: center;
    height: 40px;
  }
  .contacts .icon {
    width: 32px;
    height: 32px;
    margin-right: 16px;
    flex: none;
  }
  .contacts .email { font-size: 28px; }
  .contacts .label { color: var(--primary); margin-left: 10px; }
  .portrait {
    position: absolute;
    left: 640px;
    top: 32px;
    width: 460px;
    height: 600px;
    border-top-left-radius: 120px;
    background: linear-gradient(180deg, var(--photo-top), var(--photo-bottom));
  }
  .waves {
    position: absolute;
    left: 0;
    top: 0;
    width: 1100px;
    height: 680px;
  }
</style>
</head>
<body>
  <div class="card">
    <div class="portrait" role="img" aria-label="Portrait photo of Marlene Agate, smiling and gesturing toward the contact details"></div>

    <svg class="waves" viewBox="0 0 1100 680" aria-hidden="true">
      <path d="M0 516 C160 476 360 460 520 505 C600 530 650 560 700 585 L700 680 L0 680 Z" fill="var(--accent)"/>
      <path d="M0 575 C180 500 420 500 620 560 C800 615 960 640 1100 612 L1100 680 L0 680 Z" fill="var(--primary)"/>
      <path d="M0 575 C180 500 420 500 620 560 C800 615 960 640 1100 612" fill="none" stroke="var(--paper)" stroke-width="7"/>
    </svg>

    <div class="accent-bar"></div>
    <h1 class="name">MARLENE AGATE</h1>
    <p class="title">Commercial Loan Originator</p>

    <ul class="contacts">
      <li>
        <svg class="icon" viewBox="0 0 24 24" aria-hidden="true"><path d="M6.6 3.5 9 6.8 7.6 8.7c.9 2.6 3 4.7 5.7 5.7l1.9-1.4 3.3 2.4-1.2 3.2c-.3.7-1 1-1.7.9C9.5 18.6 5.4 14.5 4.5 8.4c-.1-.7.2-1.4.9-1.7z" fill="none" stroke="var(--primary)" stroke-width="2" stroke-linejoin="round"/><path d="M14 3.5a6.5 6.5 0 0 1 6.5 6.5M14 7a3 3 0 0 1 3 3" fill="none" stroke="var(--primary)" stroke-width="1.8" stroke-linecap="round"/></svg>
        <span>(800) 417-2906 x68</span>
      </li>
      <li>
        <svg class="icon" viewBox="0 0 24 24" aria-hidden="true"><path d="M6.6 3.5 9 6.8 7.6 8.7c.9 2.6 3 4.7 5.7 5.7l1.9-1.4 3.3 2.4-1.2 3.2c-.3.7-1 1-1.7.9C9.5 18.6 5.4 14.5 4.5 8.4c-.1-.7.2-1.4.9-1.7z" fill="none" stroke="var(--primary)" stroke-width="2" stroke-linejoin="round"/><path d="M14 3.5a6.5 6.5 0 0 1 6.5 6.5M14 7a3 3 0 0 1 3 3" fill="none" stroke="var(--primary)" stroke-width="1.8" stroke-linecap="round"/></svg>
        <span>(240) 615-2043</span><span class="label">(Direct )</span>
      </li>
      <li class="email">
        <svg class="icon" viewBox="0 0 24 24" aria-hidden="true"><rect x="2" y="5.5" width="20" height="13" fill="var(--primary)"/><path d="M2.5 6 12 13l9.5-7M2.5 18l7-6M21.5 18l-7-6" fill="none" stroke="var(--paper)" stroke-width="1.4"/></svg>
        <span>freshgreens4life@quillbox.example</span>
      </li>
    </ul>
  </div>
</body>
</html>
```